Navoro & Omvar Automotive Repair Shop. Need a new website design.

We specialize in Navoro & Omvar auto repair, but also work on other Asian import vehicles. We have been in business for 7 years and pride ourselves on high quality auto repair that is fixed right the first time. Would like the automotive repair website to incorporate the colors black, red and white if possible and have our logo and some Navoro and Omvar vehicles included in the website.

Target Market(s)

Navoro & Omvar vehicle owners

Industry/Entity Type

Automotive Repair

Coding

Coded - Design and coding required

Number of Pages Required

5+ page

Colors
EB3D1F
EC4F4E
F09395
F8D3D4
FCEDEE

Requirements
Must have
• Home, Services, Contact Us, Schedule appointment, and a gallery tab that I can add shop pictures to when completed.
Nice to have
• Would like to see example pictures of job next to each service listed.
Should not have
• Service not related to auto repair. Ex. auto detailing, towing, car wash

```html
<!DOCTYPE html>
<html lang="en">
<head>
<meta charset="utf-8">
<title>Corvan Automotive – Website Design</title>
<link href="https://fonts.googleapis.com/css2?family=Michroma&family=Barlow:wght@400;500;600;700&display=swap" rel="stylesheet">
<style>
:root{
  --stage:#a9a9a9;
  --black:#000;
  --ink:#0b0b0b;
  --panel:#151515;
  --panel-2:#1d1d1d;
  --red:#e3100f;
  --red-deep:#a80a0a;
  --white:#fff;
  --grey:#bdbdbd;
  --line:#4a4a4a;
  --silver:#c9c9c9;
}
*{box-sizing:border-box;margin:0;padding:0}
html,body{width:678px;height:1200px;overflow:hidden;background:var(--stage)}
body{position:relative;font-family:'Barlow',sans-serif;color:var(--white)}
.page{position:absolute;top:17.7px;width:637px;background:var(--black);transform:scale(.4657);transform-origin:0 0;overflow:hidden}
.page--full{left:29.3px;height:2499px}
.page--short{left:359.5px;height:2257px}
section,header,footer{position:relative;width:637px;overflow:hidden}
.abs{position:absolute}
.display{font-family:'Michroma',sans-serif;text-transform:uppercase;letter-spacing:.5px}
.eyebrow{font-size:7px;color:var(--red);letter-spacing:1px;text-transform:uppercase}
.red{color:var(--red)}
.btn-red{background:var(--red);color:var(--white);font-weight:700;text-transform:uppercase;display:flex;align-items:center;justify-content:center}
.btn-ghost{border:1.5px solid var(--grey);color:var(--white);font-weight:600;text-transform:uppercase;display:flex;align-items:center;justify-content:center;letter-spacing:1px}

/* header / hero */
.hero{height:400px;background:var(--black)}
.hero__photo{right:0;top:40px;width:400px;height:350px;background:radial-gradient(ellipse at 55% 45%,#8a8a8a 0%,#4b4b4b 35%,#1c1c1c 70%,#000 100%)}
.brand{display:flex;align-items:center;gap:5px;font-family:'Barlow',sans-serif;font-weight:700;color:var(--white);text-transform:uppercase}
.brand__dot{width:14px;height:14px;border-radius:50%;background:var(--red);flex:none}
.hero .brand{left:73px;top:30px;font-size:15px}
.nav{left:205px;top:27px;display:flex;gap:0;font-size:7.5px;font-weight:500;text-transform:uppercase}
.nav span{margin-right:20px;padding-bottom:3px}
.nav .is-active{border-bottom:1.5px solid var(--red)}
.nav__cta{left:460px;top:21px;width:92px;height:19px;border:1px solid var(--grey);font-size:6px;font-weight:600;display:flex;align-items:center;justify-content:center;text-transform:uppercase}
.hero__frame{left:70px;top:118px;width:70px;height:167px;border:2px solid #5a5a5a;border-right:none}
.hero__title{left:95px;top:140px;font-size:16px;line-height:21px}
.hero__sub{left:96px;top:210px;font-size:11px;font-weight:600}
.hero__btn{left:96px;top:236px;width:150px;height:26px;font-size:8px}
.hero__band{left:0;top:0}

/* about */
.about{height:285px}
.about__brand{left:60px;top:80px;width:240px;flex-direction:column;gap:8px;font-size:38px;letter-spacing:2px}
.about__brand small{font-size:16px;color:var(--red);font-weight:700;letter-spacing:2px}
.about__eyebrow{left:323px;top:26px}
.about__title{left:323px;top:38px;font-size:18px}
.about__rule{left:515px;top:48px;width:122px;height:1px;background:var(--line)}
.about__rule::before{content:"";position:absolute;left:0;top:-2px;width:5px;height:5px;background:var(--grey)}
.about__lead{left:325px;top:66px;width:280px;font-size:8.3px;font-weight:600;line-height:12.5px}
.about__body{left:325px;top:110px;width:282px;font-size:7.3px;line-height:12.3px;color:#ddd}
.about__btn{left:329px;top:223px;width:88px;height:25px;font-size:7px}

/* services */
.services{height:320px;background:linear-gradient(180deg,#1a1a1a,#121212 60%,#0f0f0f)}
.center{left:0;width:637px;text-align:center}
.services__eyebrow{top:35px}
.services__title{top:50px;font-size:17px}
.svc-col{top:92px;list-style:none;font-size:7.3px;font-weight:600;text-transform:uppercase}
.svc-col li{display:flex;gap:8px;line-height:12px;padding-bottom:12.5px;align-items:flex-start}
.svc-icon{width:14px;height:12px;flex:none;border:1.5px solid #cfcfcf;border-radius:3px}
.svc-col li.is-active{position:relative}
.svc-hl{left:52px;top:87px;width:152px;height:27px;background:var(--red);clip-path:polygon(0 0,100% 0,94% 100%,0 100%)}

/* gallery */
.gallery{height:460px;background:linear-gradient(180deg,#0b0b0b,#262626 45%,#0b0b0b)}
.chev{left:0;top:0}
.gallery__eyebrow{top:105px}
.gallery__title{top:120px;font-size:17px}
.shot{background:linear-gradient(135deg,#6d6d6d,#2e2e2e 60%,#8a8a8a)}

/* makes */
.makes{background:var(--black)}
.makes__title{top:30px;font-size:11px;line-height:13px}
.make-grid{left:70px;width:487px;height:152px;display:grid;grid-template-columns:repeat(4,1fr);grid-template-rows:repeat(2,1fr);border:1px solid #3a3a3a}
.make{border:1px solid #3a3a3a;display:flex;align-items:center;justify-content:center;gap:5px;font-size:12px;font-weight:600;letter-spacing:1.5px;text-transform:uppercase;color:var(--white)}
.make__dot{width:8px;height:8px;border-radius:50%;background:var(--white)}
.make--lit{background:linear-gradient(135deg,#f2f2f2,#a9a9a9);color:#c00}
.make--lit .make__dot{background:#c00}
.makes__btn{left:238px;width:154px;height:30px;font-size:9.5px;font-weight:600}

/* testimonials */
.reviews{height:230px;background:linear-gradient(180deg,#161616,#0d0d0d)}
.reviews__eyebrow{top:25px}
.reviews__title{top:40px;font-size:17px}
.quote{width:212px;height:104px;border:1.5px solid #3b3b3b;top:75px;text-align:center;font-size:7.5px;line-height:14px;padding:12px 22px 0}
.quote__mark{color:var(--red);font-size:18px;font-weight:700;line-height:14px;display:block}
.quote__name{font-weight:700;display:block;margin-top:6px}

/* contact */
.contact{background:linear-gradient(180deg,#0d0d0d,#262626 40%,#111)}
.contact__rule{left:28px;width:36px;height:1px;background:var(--red)}
.contact__rule::after{content:"";position:absolute;right:-3px;top:-2px;width:5px;height:5px;background:var(--red)}
.contact__title{font-size:18px}
.contact__text{width:215px;font-size:7.5px;line-height:14px;color:#ddd}
.c-row{display:flex;align-items:center;gap:9px;font-size:7.5px;line-height:13px}
.c-ico{width:15px;height:15px;border-radius:50%;background:#d9d9d9;flex:none;position:relative}
.form{width:260px;height:180px;border:1.5px solid #3b3b3b;background:rgba(0,0,0,.55);padding:18px 20px}
.form__title{font-family:'Michroma',sans-serif;font-size:8.5px;text-transform:uppercase;margin-bottom:12px}
.form__row{display:flex;gap:5px;margin-bottom:6px}
.field{flex:1;height:20px;border:1px solid #8a8a8a;font-size:5.5px;padding:4px 9px}
.field--area{height:46px}
.form__btn{width:70px;height:19px;font-size:6.5px;letter-spacing:1px}

/* footer */
.foot{background:linear-gradient(180deg,#1a1a1a,#0a0a0a)}
.foot .brand{font-size:14px}
.foot__nav{display:flex;justify-content:center;gap:22px;font-size:8.5px;font-weight:600;text-transform:uppercase;align-items:center}
.foot__nav i{width:3px;height:3px;background:var(--red);display:block}
.copy{font-size:6px;color:#ccc}
.socials{display:flex;gap:7px}
.socials span{width:11px;height:11px;border-radius:50%;background:#ddd}
.socials span:first-child{background:var(--red)}
.badges{display:flex;align-items:center}
.badge-sq{background:#e8e8e8;border-radius:2px}
.badge-red{background:var(--red);border-radius:3px}
.badge-green{background:#1aa35a;border-radius:8px}
.badge-blue{background:#2c4f9c;border-radius:2px}
</style>
</head>
<body>

<!-- ===== Full home layout ===== -->
<main class="page page--full">
  <header class="hero">
    <div class="abs hero__photo" role="img" aria-label="Mechanic's arms working on an exposed engine block"></div>
    <svg class="abs hero__band" width="637" height="410" viewBox="0 0 637 410">
      <polygon points="0,388 320,340 637,392 637,410 0,410" fill="#000"/>
      <polygon points="0,388 320,340 637,392 637,405 320,356 0,404" fill="#e3100f"/>
    </svg>
    <div class="abs brand"><span class="brand__dot"></span>Corvan</div>
    <nav class="abs nav"><span class="is-active">Home</span><span>About Us</span><span>Services</span><span>Gallery</span><span>Contact</span></nav>
    <div class="abs nav__cta">Financing Application</div>
    <div class="abs hero__frame"></div>
    <h1 class="abs display hero__title">Specializing in<br>Navoro and Omvar<br><span class="red">Auto Repair</span></h1>
    <p class="abs hero__sub">Dealership Quality at an affordable price.</p>
    <div class="abs btn-red hero__btn">Schedule an Appointment</div>
  </header>

  <section class="about">
    <div class="abs brand about__brand">Corvan<small>Automotive</small></div>
    <p class="abs eyebrow about__eyebrow">Our Company</p>
    <h2 class="abs display about__title">About Corvan</h2>
    <div class="abs about__rule"></div>
    <p class="abs about__lead">Corvan Automotive is a locally owned and operated auto repair shop in Brookfield that offers comprehensive car care and services for Navoro &amp; Omvar and all other Asian imports vehicles.</p>
    <p class="abs about__body">Led by an NCMT master certified technician with 20 years experience working for Navoro &amp; Omvar dealerships, our auto shop is your go to facility for everything from factory auto maintenance, including oil changes, fluid services and tune ups, to complex engine repairs, hybrid diagnostic &amp; repair, brake jobs, etc. We have state of the art equipment and tools to ensure that we can properly diagnose and repair your vehicle to get you back on the road quickly. Our work comes with a warranty and we offer towing if needed. We also offer discounts for RideGo &amp; Hopcar rides.</p>
    <div class="abs btn-ghost about__btn">Learn More</div>
  </section>

  <section class="services">
    <p class="abs eyebrow center services__eyebrow">What we do</p>
    <h2 class="abs display center services__title">Services Provide</h2>
    <div class="abs svc-hl"></div>
    <ul class="abs svc-col" style="left:66px">
      <li><span class="svc-icon"></span>Oil Changes</li>
      <li><span class="svc-icon"></span>Computer Diagnostics</li>
      <li><span class="svc-icon"></span>Electrical Specialists</li>
      <li><span class="svc-icon"></span>Tires</li>
      <li><span class="svc-icon"></span>Tire Balance &amp; Rotations</li>
      <li><span class="svc-icon"></span>Pre Purchase Inspections</li>
      <li><span class="svc-icon"></span>Insurance Claims</li>
      <li><span class="svc-icon"></span>Emission Repair &amp; Catalytic<br>Converters</li>
    </ul>
    <ul class="abs svc-col" style="left:228px">
      <li><span class="svc-icon"></span>Engine Repair</li>
      <li><span class="svc-icon"></span>Heating &amp; AC Repair</li>
      <li><span class="svc-icon"></span>State Inspection</li>
      <li><span class="svc-icon"></span>Suspension Service &amp; Repair</li>
      <li><span class="svc-icon"></span>Leveling Kits &amp; Minor Lift Kit<br>Installation</li>
      <li><span class="svc-icon"></span>Brakes Service &amp; Repair</li>
      <li><span class="svc-icon"></span>Exhaust, Muffler Service &amp; Repair</li>
      <li><span class="svc-icon"></span>Automatic, Manual, Computerized<br>Transmission Service &amp; Repair</li>
    </ul>
    <ul class="abs svc-col" style="left:418px">
      <li><span class="svc-icon"></span>Clutch Service &amp; Repair</li>
      <li><span class="svc-icon"></span>CV Axle Service &amp; Repair</li>
      <li><span class="svc-icon"></span>Fuel Injection System Service<br>Cleaning &amp; Repair</li>
      <li><span class="svc-icon"></span>Timing Belts &amp; Water Pumps</li>
      <li><span class="svc-icon"></span>Radiators &amp; Fans Service &amp; Repair</li>
      <li><span class="svc-icon"></span>Tune Ups &amp; Factory Scheduled<br>Maintenance</li>
      <li><span class="svc-icon"></span>Hybrid Vehicle Diagnostic &amp; Repair<br>24-HR Night Drop</li>
    </ul>
  </section>

  <section class="gallery">
    <svg class="abs chev" width="637" height="80" viewBox="0 0 637 80">
      <polygon points="0,0 637,0 637,8 318,72 0,8" fill="#121212"/>
      <polyline points="0,8 318,72 637,8" fill="none" stroke="#9a9a9a" stroke-width="6"/>
    </svg>
    <p class="abs eyebrow center gallery__eyebrow">Photo Gallery</p>
    <h2 class="abs display center gallery__title">Our Gallery</h2>
    <div class="abs shot" style="left:57px;top:152px;width:171px;height:127px" role="img" aria-label="Technician working under a lifted vehicle"></div>
    <div class="abs shot" style="left:235px;top:152px;width:171px;height:127px" role="img" aria-label="Open hood of a luxury SUV in the shop"></div>
    <div class="abs shot" style="left:413px;top:152px;width:171px;height:127px" role="img" aria-label="Engine removed and placed on a stand"></div>
    <div class="abs shot" style="left:57px;top:287px;width:260px;height:127px" role="img" aria-label="Silver pickup truck on a lift with wheels removed"></div>
    <div class="abs shot" style="left:325px;top:287px;width:259px;height:127px" role="img" aria-label="Row of SUVs parked in front of the shop"></div>
  </section>

  <section class="makes" style="height:325px">
    <h2 class="abs display center makes__title">Corvan Automotive specializes in Navoro &amp; Omvar<br>auto repair but also service and repair<br>the following makes</h2>
    <div class="abs make-grid" style="top:92px">
      <div class="make"><span class="make__dot"></span>Altora</div>
      <div class="make"><span class="make__dot"></span>Havenmark</div>
      <div class="make"><span class="make__dot"></span>Ilvane</div>
      <div class="make"><span class="make__dot"></span>Kivo</div>
      <div class="make make--lit"><span class="make__dot"></span>Mirutek</div>
      <div class="make"><span class="make__dot"></span>Marzo</div>
      <div class="make"><span class="make__dot"></span>Nesso</div>
      <div class="make"><span class="make__dot"></span>Harlo</div>
    </div>
    <div class="abs btn-red makes__btn" style="top:273px">Financing Application</div>
  </section>

  <section class="reviews">
    <p class="abs eyebrow center reviews__eyebrow">Reviews</p>
    <h2 class="abs display center reviews__title">Testimonials</h2>
    <div class="abs quote" style="left:102px"><span class="quote__mark">”</span>I would highly recommend Corvan Automotive to family, friends, &amp; co-workers! I'm a repeat customer myself!<span class="quote__name">DANIEL R.</span></div>
    <div class="abs quote" style="left:325px"><span class="quote__mark">”</span>Corvan Automotive is my go to car repair company. I trust them with all my vehicle needs.<span class="quote__name">SOFIA M.</span></div>
  </section>

  <section class="contact" style="height:320px" role="img" aria-label="Dark shop interior with a parked car in the background">
    <div class="abs contact__rule" style="top:60px"></div>
    <p class="abs eyebrow" style="left:70px;top:48px">Get in touch</p>
    <h2 class="abs display contact__title" style="left:70px;top:60px">Contact <span class="red">Us</span></h2>
    <p class="abs contact__text" style="left:70px;top:92px">Contact us for a free estimate! Please include year, make, and model and the service or repair you would like repair you would like an estimate on.</p>
    <div class="abs c-row" style="left:72px;top:144px"><span class="c-ico"></span>hello@corvanauto.com</div>
    <div class="abs c-row" style="left:72px;top:172px"><span class="c-ico"></span>OFFICE. 555.013.9110<br>CELL. 555.028.7493</div>
    <div class="abs c-row" style="left:72px;top:212px"><span class="c-ico"></span>Mon to Fri 8.30 am to 6 pm</div>
    <div class="abs form" style="left:315px;top:48px">
      <p class="form__title">Leave us a message</p>
      <div class="form__row"><div class="field">First Name*</div><div class="field">Last Name*</div></div>
      <div class="form__row"><div class="field">Email address*</div><div class="field">Phone*</div></div>
      <div class="form__row"><div class="field field--area">Message</div></div>
      <div class="btn-red form__btn">Submit</div>
    </div>
  </section>

  <footer class="foot" style="height:159px">
    <svg class="abs chev" width="637" height="40" viewBox="0 0 637 40">
      <polygon points="0,30 318,0 637,30 637,0 0,0" fill="#0f0f0f"/>
      <polyline points="0,30 318,0 637,30" fill="none" stroke="#9a9a9a" stroke-width="5"/>
    </svg>
    <div class="abs brand" style="left:278px;top:12px"><span class="brand__dot"></span>Corvan</div>
    <nav class="abs foot__nav center" style="top:52px"><span>Home</span><i></i><span>About Us</span><i></i><span>Our Services</span><i></i><span>Gallery</span><i></i><span>Contact</span></nav>
    <p class="abs copy" style="left:88px;top:80px">Copyright © 2024 Corvan Automotive. All rights reserved.</p>
    <div class="abs socials" style="left:470px;top:82px"><span></span><span></span><span></span><span></span></div>
    <div class="abs badges" style="left:90px;top:108px;gap:46px">
      <div class="badge-red" style="width:55px;height:26px"></div>
      <div class="badge-red" style="width:48px;height:14px"></div>
      <div class="badge-blue" style="width:24px;height:34px"></div>
      <div class="badge-green" style="width:80px;height:16px"></div>
      <div class="badge-sq" style="width:28px;height:28px"></div>
    </div>
  </footer>
</main>

<!-- ===== Alternate home layout ===== -->
<main class="page page--short">
  <header class="hero">
    <div class="abs hero__photo" role="img" aria-label="Mechanic's arms working on an exposed engine block"></div>
    <svg class="abs hero__band" width="637" height="410" viewBox="0 0 637 410">
      <polygon points="0,388 320,340 637,392 637,410 0,410" fill="#000"/>
      <polygon points="0,388 320,340 637,392 637,405 320,356 0,404" fill="#e3100f"/>
    </svg>
    <div class="abs brand"><span class="brand__dot"></span>Corvan</div>
    <nav class="abs nav"><span class="is-active">Home</span><span>About Us</span><span>Services</span><span>Gallery</span><span>Contact</span></nav>
    <div class="abs nav__cta">Financing Application</div>
    <div class="abs hero__frame"></div>
    <h1 class="abs display hero__title">Specializing in<br>Navoro and Omvar<br><span class="red">Auto Repair</span></h1>
    <p class="abs hero__sub" style="font-weight:500">Dealership Quality at an affordable price.</p>
    <div class="abs btn-red hero__btn" style="top:232px">Schedule an Appointment</div>
  </header>

  <section class="about">
    <div class="abs brand about__brand">Corvan<small>Automotive</small></div>
    <p class="abs eyebrow about__eyebrow">Our Company</p>
    <h2 class="abs display about__title">About Corvan</h2>
    <div class="abs about__rule"></div>
    <p class="abs about__lead">Corvan Automotive is a locally owned and operated auto repair shop in Brookfield that offers comprehensive car care and services for Navoro &amp; Omvar and all other Asian imports vehicles.</p>
    <p class="abs about__body">Led by an NCMT master certified technician with 20 years experience working for Navoro &amp; Omvar dealerships, our auto shop is your go to facility for everything from factory auto maintenance, including oil changes, fluid services and tune ups, to complex engine repairs, hybrid diagnostic &amp; repair, brake jobs, etc. We have state of the art equipment and tools to ensure that we can properly diagnose and repair your vehicle to get you back on the road quickly. Our work comes with a warranty and we offer towing if needed. We also offer discounts for RideGo &amp; Hopcar rides.</p>
    <div class="abs btn-ghost about__btn">Learn More</div>
  </section>

  <section class="services">
    <p class="abs eyebrow center services__eyebrow">What we do</p>
    <h2 class="abs display center services__title">Services Provide</h2>
    <div class="abs svc-hl"></div>
    <ul class="abs svc-col" style="left:66px">
      <li><span class="svc-icon"></span>Oil Changes</li>
      <li><span class="svc-icon"></span>Computer Diagnostics</li>
      <li><span class="svc-icon"></span>Electrical Specialists</li>
      <li><span class="svc-icon"></span>Tires</li>
      <li><span class="svc-icon"></span>Tire Balance &amp; Rotations</li>
      <li><span class="svc-icon"></span>Pre Purchase Inspections</li>
      <li><span class="svc-icon"></span>Insurance Claims</li>
      <li><span class="svc-icon"></span>Emission Repair &amp; Catalytic<br>Converters</li>
    </ul>
    <ul class="abs svc-col" style="left:228px">
      <li><span class="svc-icon"></span>Engine Repair</li>
      <li><span class="svc-icon"></span>Heating &amp; AC Repair</li>
      <li><span class="svc-icon"></span>State Inspection</li>
      <li><span class="svc-icon"></span>Suspension Service &amp; Repair</li>
      <li><span class="svc-icon"></span>Leveling Kits &amp; Minor Lift Kit<br>Installation</li>
      <li><span class="svc-icon"></span>Brakes Service &amp; Repair</li>
      <li><span class="svc-icon"></span>Exhaust, Muffler Service &amp; Repair</li>
      <li><span class="svc-icon"></span>Automatic, Manual, Computerized<br>Transmission Service &amp; Repair</li>
    </ul>
    <ul class="abs svc-col" style="left:418px">
      <li><span class="svc-icon"></span>Clutch Service &amp; Repair</li>
      <li><span class="svc-icon"></span>CV Axle Service &amp; Repair</li>
      <li><span class="svc-icon"></span>Fuel Injection System Service<br>Cleaning &amp; Repair</li>
      <li><span class="svc-icon"></span>Timing Belts &amp; Water Pumps</li>
      <li><span class="svc-icon"></span>Radiators &amp; Fans Service &amp; Repair</li>
      <li><span class="svc-icon"></span>Tune Ups &amp; Factory Scheduled<br>Maintenance</li>
      <li><span class="svc-icon"></span>Hybrid Vehicle Diagnostic &amp; Repair<br>24-HR Night Drop</li>
    </ul>
  </section>

  <section class="gallery">
    <svg class="abs chev" width="637" height="80" viewBox="0 0 637 80">
      <polygon points="0,0 637,0 637,8 318,72 0,8" fill="#121212"/>
      <polyline points="0,8 318,72 637,8" fill="none" stroke="#9a9a9a" stroke-width="6"/>
    </svg>
    <p class="abs eyebrow center gallery__eyebrow">Photo Gallery</p>
    <h2 class="abs display center gallery__title">Our Gallery</h2>
    <div class="abs shot" style="left:57px;top:150px;width:171px;height:127px" role="img" aria-label="Technician working under a lifted vehicle"></div>
    <div class="abs shot" style="left:235px;top:150px;width:171px;height:127px" role="img" aria-label="Open hood of a luxury SUV in the shop"></div>
    <div class="abs shot" style="left:413px;top:150px;width:171px;height:127px" role="img" aria-label="Engine removed and placed on a stand"></div>
    <div class="abs shot" style="left:57px;top:285px;width:260px;height:127px" role="img" aria-label="Silver pickup truck on a lift with wheels removed"></div>
    <div class="abs shot" style="left:325px;top:285px;width:259px;height:127px" role="img" aria-label="Row of SUVs parked in front of the shop"></div>
  </section>

  <section class="makes" style="height:335px">
    <h2 class="abs display center makes__title" style="top:38px">Corvan Automotive specializes in Navoro &amp; Omvar<br>auto repair but also service and repair<br>the following makes</h2>
    <div class="abs make-grid" style="top:97px">
      <div class="make"><span class="make__dot"></span>Altora</div>
      <div class="make"><span class="make__dot"></span>Havenmark</div>
      <div class="make"><span class="make__dot"></span>Ilvane</div>
      <div class="make"><span class="make__dot"></span>Kivo</div>
      <div class="make make--lit"><span class="make__dot"></span>Mirutek</div>
      <div class="make"><span class="make__dot"></span>Marzo</div>
      <div class="make"><span class="make__dot"></span>Nesso</div>
      <div class="make"><span class="make__dot"></span>Harlo</div>
    </div>
    <div class="abs btn-red makes__btn" style="top:269px">Financing Application</div>
  </section>

  <section class="contact" style="height:285px" role="img" aria-label="Dark shop interior with a parked car in the background">
    <div class="abs contact__rule" style="top:92px"></div>
    <p class="abs eyebrow" style="left:70px;top:80px">Get in touch</p>
    <h2 class="abs display contact__title" style="left:70px;top:92px">Contact <span class="red">Us</span></h2>
    <p class="abs contact__text" style="left:70px;top:124px">Contact us for a free estimate! Please include year, make, and model and the service or repair you would like repair you would like an estimate on.</p>
    <div class="abs btn-ghost" style="left:74px;top:180px;width:142px;height:25px;font-size:6.5px;letter-spacing:.5px">Schedule an Appointment</div>
    <div class="abs form" style="left:315px;top:48px;height:172px">
      <p class="form__title">Leave us a message</p>
      <div class="form__row"><div class="field">First Name*</div><div class="field">Last Name*</div></div>
      <div class="form__row"><div class="field">Email address*</div><div class="field">Phone*</div></div>
      <div class="form__row"><div class="field field--area">Message</div></div>
      <div class="btn-red form__btn">Submit</div>
    </div>
  </section>

  <footer class="foot" style="height:172px">
    <svg class="abs chev" width="637" height="40" viewBox="0 0 637 40">
      <polygon points="0,30 318,0 637,30 637,0 0,0" fill="#0f0f0f"/>
      <polyline points="0,30 318,0 637,30" fill="none" stroke="#9a9a9a" stroke-width="5"/>
    </svg>
    <div class="abs brand" style="left:278px;top:24px"><span class="brand__dot"></span>Corvan</div>
    <nav class="abs foot__nav center" style="top:86px"><span>Home</span><i></i><span>About Us</span><i></i><span>Our Services</span><i></i><span>Gallery</span><i></i><span>Contact</span></nav>
    <p class="abs copy" style="left:88px;top:117px">© 2024 Corvan Automotive. All rights reserved.</p>
    <div class="abs socials" style="left:88px;top:134px"><span></span><span></span><span></span><span></span></div>
    <div class="abs badges" style="left:245px;top:113px;gap:22px">
      <div class="badge-sq" style="width:28px;height:28px"></div>
      <div class="badge-red" style="width:45px;height:24px"></div>
      <div class="badge-red" style="width:58px;height:12px"></div>
      <div class="badge-blue" style="width:22px;height:30px"></div>
      <div class="badge-green" style="width:66px;height:14px"></div>
    </div>
  </footer>
</main>

</body>
</html>
```